Best local air conditioning and heating contractor

We need a website design for a new company in Tampa Bay called Coastal Breeze Air Conditioning Company. We provide superior services for residential and commercial properties as well as maintenance and installing HVAC systems. We also want to sell equipment, parts and filter on the website as well. We want it easy to use for customers. Rich with content and keywords for our area.

Target Market(s)

homeowners in Tampa Bay

Industry/Entity Type

HVAC air conditioning and heating

Coding

Coded - Design and coding required

Number of Pages Required

5+ page

Font styles to use
Sans Serif

Requirements
Nice to have
• would like the colors to be same as logo

```html
<!DOCTYPE html>
<html lang="en">
<head>
<meta charset="utf-8">
<title>Coastal Breeze Cooling Company</title>
<link rel="stylesheet" href="https://fonts.googleapis.com/css2?family=Krona+One&family=Roboto:wght@400;500;700&display=swap">
<style>
:root{
  --red:#e0262c;
  --navy:#1c3479;
  --blue:#35498f;
  --ink:#111;
  --text:#333;
  --light:#f3f3f3;
  --footer:#0c0c0e;
  --head:"Krona One",sans-serif;
  --body:"Roboto",sans-serif;
}
*{box-sizing:border-box;margin:0;padding:0}
html,body{width:1200px;height:4239px;overflow:hidden;background:#fff}
body{font-family:var(--body);color:var(--text);position:relative}
.abs{position:absolute}
.bar{width:40px;height:6px;background:var(--red)}
.h2{font-family:var(--head);font-size:33px;color:var(--ink);letter-spacing:1px;text-transform:uppercase}
.btn{position:absolute;display:flex;align-items:center;justify-content:center;font-family:var(--head);font-size:15px;color:#fff;border-radius:28px;letter-spacing:.5px;text-transform:uppercase}
.btn-red{background:var(--red)}
.btn-navy{background:var(--navy)}

/* header */
.topbar{position:absolute;left:0;top:0;width:1200px;height:76px;background:#fff}
.contact{position:absolute;top:20px;display:flex;align-items:center;gap:14px;font-size:15px}
.contact .ic{width:38px;height:38px;border-radius:50%;display:flex;align-items:center;justify-content:center}
.contact small{display:block;font-size:14px;color:var(--red)}
.navbar{position:absolute;left:0;top:76px;width:1200px;height:56px;background:var(--red)}
.nav{position:absolute;left:492px;top:17px;display:flex;gap:34px;color:#fff;font-size:15px}
.logo-blob{position:absolute;left:82px;top:0;width:330px;height:148px;background:#fff;border-radius:0 0 165px 165px}
.brand{position:absolute;left:124px;top:34px;width:250px;font-family:var(--body);font-weight:700;font-size:21px;line-height:1.15;color:var(--navy);text-align:center;text-transform:uppercase}

/* hero */
.hero{position:absolute;left:0;top:132px;width:1200px;height:600px}
.hero-photo{position:absolute;inset:0;background:linear-gradient(90deg,#2e4386 0%,#465a98 40%,#8a8f9c 62%,#b4a99b 100%)}
.hero-kicker{position:absolute;left:150px;top:104px;font-family:var(--head);font-size:18px;color:#1d2a55}
.hero-title{position:absolute;left:110px;top:140px;font-family:var(--head);font-size:52px;line-height:66px;color:#fff}
.hero-title span{display:block;color:var(--red)}
.hero-text{position:absolute;left:113px;top:272px;width:400px;font-size:12.5px;line-height:23px;color:#fff}

/* parts */
.parts{position:absolute;left:0;top:732px;width:1200px;height:664px;background:linear-gradient(180deg,#f7f7f7,#fff 50%,#f6f6f6)}
.part{position:absolute;width:300px;text-align:center}
.part .circle{width:222px;height:222px;border-radius:50%;background:var(--light);margin:0 auto;display:flex;align-items:center;justify-content:center}
.part .thumb{width:120px;height:90px;border-radius:10px}
.part h3{font-family:var(--head);font-size:20px;color:var(--ink);margin-top:30px}
.part p{font-size:12.5px;line-height:28px;margin:14px auto 0;width:250px}

/* split */
.split{position:absolute;left:0;top:1396px;width:1200px;height:459px}
.split h3{position:absolute;font-family:var(--head);font-size:31px;line-height:42px;color:#fff}
.split p{position:absolute;width:430px;font-size:16px;line-height:28px;color:#fff}

/* about */
.about-photo{position:absolute;left:112px;top:1933px;width:414px;height:414px;border-radius:50%;background:radial-gradient(circle at 40% 40%,#9a9590,#5d5d62 70%,#3e4046)}
.about p{position:absolute;left:571px;width:540px;font-size:13.5px;line-height:30px}

/* testimonial */
.testi{position:absolute;left:0;top:2458px;width:1200px;height:564px;background:linear-gradient(180deg,#34488e,#3d5195 60%,#2f4384)}
.testi-frame{position:absolute;left:530px;top:68px;width:145px;height:140px;border:5px solid rgba(255,255,255,.25)}
.testi-title{position:absolute;left:0;width:1200px;top:108px;text-align:center;font-family:var(--head);font-size:32px;color:#fff}
.testi-title span{color:var(--red)}
.quote{position:absolute;width:450px;color:#fff}
.quote p{font-size:17.5px;line-height:29px}
.quote .stars{margin-top:14px;color:#f6b81a;font-size:17px;letter-spacing:1px}
.quote h4{font-family:var(--head);font-size:15px;margin-top:10px}
.quote small{font-size:12.5px}

/* request */
.field{position:absolute;height:51px;background:#fff;box-shadow:0 2px 10px rgba(0,0,0,.08);font-size:14px;color:#777;padding:17px 20px;display:flex;align-items:flex-start;gap:7px}

/* footer */
.footer{position:absolute;left:0;top:3791px;width:1200px;height:448px;background:var(--footer);color:#fff}
.footer h5{position:absolute;top:93px;font-family:var(--head);font-size:15px}
.links{position:absolute;top:133px;font-size:13px;line-height:30px;list-style:none}
.social{position:absolute;top:227px;width:30px;height:30px;border:1.5px solid #fff;border-radius:50%}
.fc{position:absolute;left:847px;font-size:13px;line-height:17px}
.fc b{display:block}
</style>
</head>
<body>

<header>
  <div class="topbar">
    <div class="contact" style="left:428px"><span class="ic" style="background:var(--red)"><svg width="16" height="16" viewBox="0 0 24 24"><path fill="#fff" d="M6.6 10.8a15 15 0 006.6 6.6l2.2-2.2c.3-.3.7-.4 1-.2 1.1.4 2.3.6 3.6.6.6 0 1 .4 1 1V20c0 .6-.4 1-1 1A17 17 0 013 4c0-.6.4-1 1-1h3.5c.6 0 1 .4 1 1 0 1.3.2 2.5.6 3.6.1.3 0 .7-.2 1z"/></svg></span><div><small>Call Us</small>+1 813 555 0142</div></div>
    <div class="contact" style="left:648px"><span class="ic" style="background:var(--navy)"><svg width="16" height="16" viewBox="0 0 24 24"><path fill="#fff" d="M3 5h18v14H3z"/><path fill="none" stroke="#1c3479" stroke-width="2" d="M3 6l9 7 9-7"/></svg></span><div><small>Email</small>info@coastalbreezecooling.com</div></div>
    <div class="contact" style="left:879px;font-size:14px"><span class="ic" style="background:var(--red)"><svg width="16" height="18" viewBox="0 0 24 24"><path fill="#fff" d="M12 2a7 7 0 00-7 7c0 5 7 13 7 13s7-8 7-13a7 7 0 00-7-7zm0 9.5a2.5 2.5 0 110-5 2.5 2.5 0 010 5z"/></svg></span><div style="line-height:18px">12/B Bayshore Blvd<br>Tampa Bay, Florida</div></div>
  </div>
  <div class="navbar">
    <nav class="nav"><span>Home</span><span>About Us</span><span>Our Services</span><span>Our Parts and Filters</span><span>Contact Us</span></nav>
  </div>
  <div class="logo-blob"></div>
  <div class="brand">Coastal Breeze Cooling Company</div>
</header>

<section class="hero">
  <div class="hero-photo" role="img" aria-label="HVAC technician smiling while servicing an outdoor air conditioning unit"></div>
  <div class="hero-kicker">WELCOME TO</div>
  <h1 class="hero-title">COASTAL<span>BREEZE</span></h1>
  <p class="hero-text">Lorem ipsum dolor sit amet, consectetur adipiscing elit, sed do eiusmod tempor incididunt ut labore et dolore magna aliqua. Quis ipsum suspendisse ultrices gravida.</p>
  <div class="btn btn-red" style="left:111px;top:354px;width:224px;height:55px;border-radius:6px">Get Started</div>
</section>

<section class="parts">
  <h2 class="h2 abs" style="left:0;width:1200px;text-align:center;top:62px">Our Parts and Filters</h2>
  <div class="bar abs" style="left:578px;top:118px"></div>
  <svg class="abs" style="left:50px;top:322px" width="18" height="26" viewBox="0 0 18 26"><path d="M13 3L4 13l9 10" fill="none" stroke="#111" stroke-width="2.5"/></svg>
  <svg class="abs" style="left:1128px;top:322px" width="18" height="26" viewBox="0 0 18 26"><path d="M5 3l9 10-9 10" fill="none" stroke="#111" stroke-width="2.5"/></svg>
  <div class="part" style="left:156px;top:177px"><div class="circle"><div class="thumb" role="img" aria-label="Stove radiator" style="background:linear-gradient(135deg,#555,#1d1d1d)"></div></div><h3>STOVE RADIATOR</h3><p>Lorem ipsum dolor sit amet, consectetur adipiscing elit, sed do eiusmod tempor incididunt ut labore et</p></div>
  <div class="part" style="left:460px;top:177px"><div class="circle"><div class="thumb" role="img" aria-label="AC compressor" style="background:linear-gradient(135deg,#5fb0d8,#1f5f8c)"></div></div><h3>AC COMPRESSOR</h3><p>Lorem ipsum dolor sit amet, consectetur adipiscing elit, sed do eiusmod tempor incididunt ut labore et</p></div>
  <div class="part" style="left:785px;top:177px"><div class="circle"><div class="thumb" role="img" aria-label="Cylindrical air filter" style="background:linear-gradient(180deg,#e8e8e8,#a9a9a9);border-radius:45px"></div></div><h3 style="font-family:var(--body);font-weight:700;font-size:21px">AIR FILTER</h3><p>Lorem ipsum dolor sit amet, consectetur adipiscing elit, sed do eiusmod tempor incididunt ut labore et</p></div>
</section>

<section class="split">
  <svg class="abs" style="left:0;top:0" width="1200" height="459" viewBox="0 0 1200 459" role="img" aria-label="Residential and commercial interior scenes">
    <rect width="1200" height="459" fill="#3a4c8e"/>
    <polygon points="616,0 1200,0 1200,459 554,459" fill="#fff"/>
    <polygon points="630,0 1200,0 1200,459 566,459" fill="#e03a40"/>
  </svg>
  <h3 style="left:107px;top:60px">RESIDENTIAL<br>PROPERTIES</h3>
  <div class="bar abs" style="left:110px;top:152px"></div>
  <p style="left:110px;top:182px">Lorem ipsum dolor sit amet, consectetur adipiscing elit, sed do eiusmod tempor incididunt ut labore et dolore magna aliqua. Quis ipsum suspendisse ultrices gravida. Risus commodo viverra maecenas accumsan lacus vel facilisis.</p>
  <div class="btn btn-red" style="left:107px;top:361px;width:212px;height:53px">Learn More</div>
  <h3 style="left:661px;top:55px">COMMERCIAL<br>PROPERTIES</h3>
  <div class="bar abs" style="left:661px;top:148px;background:var(--navy)"></div>
  <p style="left:661px;top:176px">Lorem ipsum dolor sit amet, consectetur adipiscing elit, sed do eiusmod tempor incididunt ut labore et dolore magna aliqua. Quis ipsum suspendisse ultrices gravida. Risus commodo viverra maecenas accumsan lacus vel facilisis.</p>
  <div class="btn btn-navy" style="left:659px;top:355px;width:210px;height:53px">Learn More</div>
</section>

<section class="about">
  <div class="about-photo" role="img" aria-label="Technician repairing a commercial air conditioning unit"></div>
  <h2 class="h2 abs" style="left:571px;top:1962px">About Us</h2>
  <div class="bar abs" style="left:572px;top:2015px"></div>
  <p style="top:2034px">Lorem ipsum dolor sit amet, consectetur adipiscing elit, sed do eiusmod tempor incididunt ut labore et dolore magna aliqua. Quis ipsum suspendisse ultrices gravida. Risus commodo viverra maecenas accumsan lacus vel facilisis.</p>
  <p style="top:2154px">Lorem ipsum dolor sit amet, consectetur adipiscing elit, sed do eiusmod tempor incididunt ut labore et dolore magna aliqua. Quis ipsum suspendisse ultrices gravida. Risus commodo viverra maecenas accumsan lacus vel facilisis.</p>
  <div class="btn btn-navy" style="left:561px;top:2272px;width:206px;height:54px">Learn More</div>
</section>

<section class="testi" role="img" aria-label="Rooftop HVAC equipment with a technician at work">
  <div class="testi-frame"></div>
  <h2 class="testi-title">CLIENT <span>TESTIMONIAL</span></h2>
  <p class="abs" style="left:0;width:1200px;top:158px;text-align:center;color:#fff;font-size:14px">Lorem ipsum dolor sit amet, consectetur</p>
  <div class="quote" style="left:135px;top:278px"><p>Lorem ipsum dolor sit amet, consectetur adipiscing elit, sed do eiusmod tempor incididunt ut labore Lorem ipsum dolor</p><div class="stars">★★★★★</div><h4>MARIA LOPEZ</h4><small>Lorem Ipsum</small></div>
  <div class="quote" style="left:624px;top:278px"><p>Lorem ipsum dolor sit amet, consectetur adipiscing elit, sed do eiusmod tempor incididunt ut labore Lorem ipsum dolor</p><div class="stars">★★★★★</div><h4>DANIEL REYES</h4><small>Lorem Ipsum</small></div>
</section>

<section class="request">
  <h2 class="h2 abs" style="left:0;width:1200px;text-align:center;top:3118px">Request Service</h2>
  <div class="bar abs" style="left:580px;top:3172px"></div>
  <p class="abs" style="left:300px;width:600px;top:3210px;text-align:center;font-size:14px;line-height:24px">Lorem ipsum dolor sit amet, consectetur adipiscing elit, sed do eiusmod tempor incididunt ut labore et dolore magna aliqua.</p>
  <div class="field" style="left:115px;top:3287px;width:313px">👤 Name</div>
  <div class="field" style="left:448px;top:3287px;width:311px">✉ Email</div>
  <div class="field" style="left:779px;top:3287px;width:312px">☏ Phone</div>
  <div class="field" style="left:115px;top:3355px;width:313px">⌖ Address</div>
  <div class="field" style="left:448px;top:3355px;width:311px">▦ City</div>
  <div class="field" style="left:779px;top:3355px;width:312px">◈ Zip</div>
  <div class="field" style="left:115px;top:3427px;width:976px;height:170px">▭ Comments</div>
  <div class="btn btn-red" style="left:517px;top:3651px;width:166px;height:49px">Submit</div>
</section>

<footer class="footer">
  <div class="abs" style="left:112px;top:92px;width:240px;font-weight:700;font-size:21px;line-height:1.15;color:var(--red);text-align:center;text-transform:uppercase">Coastal Breeze Cooling Company</div>
  <span class="social" style="left:151px"></span><span class="social" style="left:192px"></span><span class="social" style="left:232px"></span><span class="social" style="left:273px"></span>
  <h5 style="left:402px">QUICK LINKS</h5>
  <ul class="links" style="left:402px"><li>Home</li><li>About Us</li><li>Our Services</li><li>Our Parts and Filters</li><li>Contact Us</li></ul>
  <h5 style="left:578px">ABOUT COMPANY</h5>
  <ul class="links" style="left:581px"><li>Legal Information</li><li>Terms &amp; Condition</li><li>Privacy Policy</li><li>Support</li></ul>
  <h5 style="left:813px">CONTACT US</h5>
  <svg class="abs" style="left:823px;top:127px" width="13" height="13" viewBox="0 0 24 24"><path fill="var(--red)" d="M6.6 10.8a15 15 0 006.6 6.6l2.2-2.2c.3-.3.7-.4 1-.2 1.1.4 2.3.6 3.6.6.6 0 1 .4 1 1V20c0 .6-.4 1-1 1A17 17 0 013 4c0-.6.4-1 1-1h3.5c.6 0 1 .4 1 1 0 1.3.2 2.5.6 3.6.1.3 0 .7-.2 1z"/></svg>
  <div class="fc" style="top:125px"><b>Phone</b>+1 (813) 555-0142</div>
  <svg class="abs" style="left:822px;top:181px" width="14" height="12" viewBox="0 0 24 20"><rect width="24" height="20" fill="var(--red)"/><path d="M1 2l11 9 11-9" fill="none" stroke="#0c0c0e" stroke-width="2"/></svg>
  <div class="fc" style="top:178px"><b>Email</b>info@coastalbreezecooling.com</div>
  <svg class="abs" style="left:823px;top:230px" width="12" height="15" viewBox="0 0 24 30"><path fill="var(--red)" d="M12 0a10 10 0 00-10 10c0 8 10 20 10 20s10-12 10-20A10 10 0 0012 0z"/></svg>
  <div class="fc" style="top:229px"><b>Location</b>199/b Bayshore Distribution<br>consectetur adipiscing elit,</div>
  <p class="abs" style="left:0;width:1200px;top:375px;text-align:center;font-size:14px">2024 Copyright Coastal Breeze Cooling | All Rights Reserved</p>
</footer>

</body>
</html>
```